Business Cards for new orthopaedic surgery practice

My husband and I are starting our own orthopaedic surgery practice. We are looking for a business card that is uniform, but one will have my name/title and the other will have his. You can just create one design with my name on it for now. But when I choose your design as the winning design I will ask that you add another copy with his name/title.

We are looking for classy, simple, elite all in one. We like dark blues/a little gold/yellow. Something that goes with our logo. We want our logo incorporated. Here is all the info you need:
Business name: RV Bone & Vitality Center
Location: 38517 North Willowmere Ave
Maple Hollow, FL 33990
Phone: 954-218-4063
Fax: 954-582-7341
Email: info@myrvbonecare.example

Names: Lydia Vance, M.D.
Board Certified Hand and Upper Extremity Surgeon

Ebo Dansu, M.D.
Board Certified Hip & Knee Replacement/General Orthopaedic Surgeon

Can decide what you want to put on the back. Maybe a slogan:
Grounded in Care. Centered on You

I am just going to upload our logo. The only thing is if we select you as the winning design, the location, and phone numbers may change. We will need your help to update that once fully solidified.

Industry/Entity Type

Medical

Contact Information for Business Card

Colors
0054AA
0677BA
7BADD7
CADEEF
E8F1F8
0094D4
00A9DD
6FCCEA
C7EBF8
E9F6FB

Requirements
Must have
• class, appeal,
Should not have
• We want to air on the side of masculine if we are looking at masculine vs. feminine feel. But we still want it classy, sophisticated, and something we will love

```html
<!DOCTYPE html>
<html lang="en">
<head>
<meta charset="utf-8">
<title>RV Bone &amp; Vitality Center – Business Cards</title>
<link rel="stylesheet" href="https://fonts.googleapis.com/css2?family=Crimson+Pro:wght@400;600;700&display=swap">
<style>
  :root {
    --navy: #1b2a52;
    --navy-faint: #2c3f6c;
    --gold: #c9a45c;
    --white: #ffffff;
    --stage: #e9ebef;
    --ink: #1b2a52;
  }
  * { box-sizing: border-box; margin: 0; padding: 0; }
  html, body { width: 1200px; height: 801px; overflow: hidden; }
  body {
    background: var(--stage);
    font-family: "Crimson Pro", Georgia, serif;
    color: var(--ink);
    position: relative;
  }
  .card {
    position: absolute;
    top: 246px;
    width: 540px;
    height: 309px;
    border-radius: 14px;
    overflow: hidden;
    border: 2px solid var(--gold);
    box-shadow: 0 10px 28px rgba(20, 30, 60, 0.22);
  }
  .card-back { left: 40px; background: var(--navy); }
  .card-front { left: 620px; background: var(--white); }

  /* back */
  .back-mark {
    position: absolute;
    left: 0; right: 0; top: 92px;
    text-align: center;
    font-size: 30px;
    font-weight: 600;
    letter-spacing: 3px;
    line-height: 1.15;
    color: var(--navy-faint);
  }
  .slogan {
    position: absolute;
    left: 0; right: 0; bottom: 40px;
    text-align: center;
    font-size: 19px;
    font-weight: 600;
    letter-spacing: 1.2px;
    color: var(--white);
  }

  /* front */
  .swoosh { position: absolute; inset: 0; width: 100%; height: 100%; }
  .brand {
    position: absolute;
    right: 26px; top: 40px;
    width: 170px;
    text-align: center;
    font-size: 19px;
    font-weight: 600;
    letter-spacing: 1.5px;
    line-height: 1.25;
    color: var(--navy);
  }
  .identity { position: absolute; left: 36px; top: 52px; width: 290px; }
  .name {
    font-size: 26px;
    font-weight: 700;
    letter-spacing: 0.5px;
    text-transform: uppercase;
    line-height: 1;
  }
  .title { font-size: 13px; margin-top: 5px; white-space: nowrap; }
  .rule { height: 1.5px; background: var(--gold); margin: 9px 0 10px; width: 290px; }
  .address { font-size: 15px; line-height: 1.3; }
  .contacts { list-style: none; margin-top: 8px; }
  .contacts li {
    display: flex; align-items: center; gap: 8px;
    font-size: 15px; line-height: 1.45;
  }
  .contacts svg { width: 13px; height: 13px; flex: none; }
  .social {
    position: absolute;
    right: 24px; bottom: 24px;
    display: flex; gap: 7px;
  }
  .social span {
    width: 20px; height: 20px; border-radius: 50%;
    background: var(--white);
  }
</style>
</head>
<body>

  <section class="card card-back" aria-label="Business card back">
    <div class="back-mark">RV BONE &amp;<br>VITALITY CENTER</div>
    <p class="slogan">Grounded in Care. Centered on You</p>
  </section>

  <section class="card card-front" aria-label="Business card front">
    <svg class="swoosh" viewBox="0 0 540 309" preserveAspectRatio="none" aria-hidden="true">
      <path d="M185 309 C350 288 430 190 540 96 L540 309 Z" fill="var(--gold)"/>
      <path d="M212 309 C370 290 436 198 540 110 L540 309 Z" fill="var(--white)"/>
      <path d="M226 309 C382 294 442 206 540 120 L540 309 Z" fill="var(--navy)"/>
    </svg>

    <div class="brand">RV BONE &amp;<br>VITALITY CENTER</div>

    <div class="identity">
      <h1 class="name">Lydia Vance, M.D.</h1>
      <p class="title">Board Certified Hand and Upper Extremity Surgeon</p>
      <div class="rule"></div>
      <p class="address">38517 North Willowmere Ave<br>Maple Hollow, FL 33990</p>
      <ul class="contacts">
        <li>
          <svg viewBox="0 0 24 24"><path fill="var(--gold)" d="M6.6 10.8a15 15 0 0 0 6.6 6.6l2.2-2.2a1 1 0 0 1 1-.25 11.4 11.4 0 0 0 3.6.57 1 1 0 0 1 1 1V20a1 1 0 0 1-1 1A17 17 0 0 1 3 4a1 1 0 0 1 1-1h3.5a1 1 0 0 1 1 1c0 1.25.2 2.45.57 3.57a1 1 0 0 1-.25 1z"/></svg>
          954-218-4063
        </li>
        <li>
          <svg viewBox="0 0 24 24"><path fill="var(--gold)" d="M7 3h10v5H7zM4 9h16a2 2 0 0 1 2 2v6h-4v4H6v-4H2v-6a2 2 0 0 1 2-2zm4 7v3h8v-3z"/></svg>
          954-582-7341
        </li>
        <li>
          <svg viewBox="0 0 24 24"><path fill="var(--gold)" d="M2 5h20v14H2zm2 2v.5l8 5 8-5V7z"/></svg>
          info@myrvbonecare.example
        </li>
        <li>
          <svg viewBox="0 0 24 24"><circle cx="12" cy="12" r="9" fill="none" stroke="var(--gold)" stroke-width="2"/><path d="M3 12h18M12 3c3 3 3 15 0 18M12 3c-3 3-3 15 0 18" fill="none" stroke="var(--gold)" stroke-width="1.6"/></svg>
          www.myrvbonecare.example
        </li>
      </ul>
    </div>

    <div class="social" aria-label="Social profiles">
      <span></span><span></span><span></span>
    </div>
  </section>

</body>
</html>
```